Brivora Distance Learning Website

Brivora provide e-learning and mixed learning solutions for individuals, colleges, organisations and B2B.
We need a modern, light and flat website design for Brivora. We want to to see the designer incorporate user experience(UX) design elements into the AI or PSD mockups. We would like to see designs that use pastel colors that compliment yellow and black of our logo.
We want our E-learning experience to accelerate learning and for the interface to be user friendly and intuitive. We want the designs to focus on quick access to course information, course reviews, learning progress and study advice. Quick and intuitive access to all content for our clients is one of our top priorities.
We would like designs for the following project 3 pages:
1. Learner homepage dashboard (see attached screenshot).
On this page the Learners need to:
- Login
- Have quick access to Packages and Courses.
- See other recommended courses (Below Packages and Courses)
- Possibly a left hand side column/menu with thumbnail icons (See lumeqa learner dashboard screenshot)
2. Homepage
See current sample
http://www.brivora-learn.example
We would like the designer to focus on creating a customized banner to enhance the home page.
3. Primary Landing/Marketing page
This page is geared towards customer acquisition with the focal point being the top banner (video or HD image).
And Course Preview content below.
See reference
http://brivora-learn.example/subscriptionPlans/marketing/MTc%3D/Mjc4Nw%3D%3D/Speaking%20Nepali%20%2B%20Nepali%20Snacks%20Bundle%20by%20Lorne%20Pike%20Vell
Other site we like:
- https://www.skillorva.example (We like the home page and top bar on courses page)
- http://www.tutorcrest.example
- http://pixelgrovelab.example (think this site looks great, love the lower graphics on the homepage)
Updates
Hello,
Thank you for taking the time to contribute to this web design competition. We would just like to point out a few things:
1. Please try to make the color palette similar to the colors used in the screenshot that we just uploaded ('possible color palette).
2. Please make the designs specific to each page: THE LEARNER HOMEPAGE, HOME PAGE, and the MARKETING LANDING PAGE.
We are very happy with the high quality of designs so far,
Cheers,
Ned Ru
VK-Studio
Also,
Please avoid using dark/bold elements in the designs. The ONLY elements that we want to be dark are the logo and the footer.
Any questions please ask,
Cheers,
Ned Ru
Vk-Studio
Hello,
Based on the round of feedback we just gave it would be great if you could complete further design changes by tomorrow, as we are pushed for time.
Thank you,
Ned Ru
VK-Studio

```html
<!DOCTYPE html>
<html lang="en">
<head>
<meta charset="utf-8">
<title>Brivora – Your Learning Journey Starts Here</title>
<link rel="stylesheet" href="https://fonts.googleapis.com/css2?family=Raleway:wght@400;500;700;800&family=Arimo:wght@400;700&display=swap">
<style>
:root{
  --yellow:#f8b91c;
  --orange:#eea21a;
  --ink:#222;
  --text:#333;
  --grey-band:#767676;
  --grey-btn:#7d7d7d;
  --footer:#333;
  --white:#fff;
}
*{box-sizing:border-box;margin:0;padding:0}
html,body{width:941px;height:1200px;overflow:hidden;background:#f7f7f7}
body{font-family:"Arimo",Arial,sans-serif;color:var(--text);position:relative}
.abs{position:absolute}

/* header */
.site-header{left:0;top:0;width:941px;height:73px;background:var(--white);border-bottom:1px solid #e2e2e2}
.brand{display:flex;align-items:center;gap:7px;font-family:"Raleway",sans-serif;font-weight:700;font-size:32px;color:var(--ink);letter-spacing:-0.5px}
.brand-dot{width:22px;height:22px;border-radius:50%;background:var(--yellow);flex:none}
.site-header .brand{left:80px;top:17px}
.btn-lang{left:676px;top:23px;width:82px;height:26px;background:var(--yellow);color:#333;font-size:12px;display:flex;align-items:center;justify-content:center;border-radius:2px;font-family:"Raleway",sans-serif;font-weight:500}
.btn-signin{left:782px;top:24px;width:69px;height:25px;background:var(--grey-btn);color:#fff;font-size:12px;display:flex;align-items:center;justify-content:center;border-radius:2px;font-family:"Raleway",sans-serif;font-weight:500}

/* hero */
.hero-bg{left:0;top:73px;width:941px;height:448px;
  background:radial-gradient(ellipse at 20% 40%,#c9a21a 0%,transparent 45%),
             radial-gradient(ellipse at 85% 25%,#f4c53a 0%,transparent 50%),
             linear-gradient(120deg,#c9a01f 0%,#e6b52c 40%,#f3c94a 70%,#f7c92f 100%)}
.hero-title{left:0;top:152px;width:941px;text-align:center;font-family:"Raleway",sans-serif;font-weight:800;font-size:39px;letter-spacing:-2px;color:#505050;text-shadow:0 1px 2px rgba(255,255,255,.35)}
.hero-sub{left:0;top:219px;width:941px;text-align:center;font-family:"Raleway",sans-serif;font-weight:500;font-size:18px;color:#2e2e2e}
.beta-card{left:285px;top:270px;width:374px;height:234px;background:rgba(250,244,222,.92);border-radius:5px}
.beta-card h2{position:absolute;left:0;top:13px;width:100%;text-align:center;font-family:"Raleway",sans-serif;font-weight:500;font-size:17px;color:#1c1c1c}
.field{position:absolute;left:56px;width:260px;background:#eee;border:1px solid #bdbdbd;font-size:10px;color:#555;padding:9px 8px}
.field-email{top:51px;height:27px;padding-top:8px}
.field-reason{top:93px;height:63px}
.btn-join{position:absolute;left:214px;top:175px;width:102px;height:33px;background:#222;color:#fff;font-family:"Raleway",sans-serif;font-weight:500;font-size:15px;display:flex;align-items:center;justify-content:center;border-radius:3px}

/* search */
.search-band{left:0;top:521px;width:941px;height:81px;background:var(--grey-band)}
.search-input{left:168px;top:545px;width:487px;height:34px;background:#fff;font-size:12px;color:#555;padding:10px 14px}
.search-btn{left:655px;top:545px;width:104px;height:34px;background:var(--yellow);color:#222;font-family:"Raleway",sans-serif;font-weight:500;font-size:18px;display:flex;align-items:center;justify-content:center}

/* packages heading */
.section-title{left:78px;top:632px;width:784px;height:40px;display:flex;align-items:center;gap:4px}
.section-title .rule{flex:1;height:1px;background:#888}
.section-title h2{font-family:"Raleway",sans-serif;font-weight:500;font-size:31px;color:#333}

/* categories */
.categories{left:78px;top:698px;width:185px;height:384px;background:#fff;box-shadow:0 1px 3px rgba(0,0,0,.25)}
.categories h3{height:39px;background:var(--yellow);font-family:"Raleway",sans-serif;font-weight:500;font-size:19px;color:#222;padding:7px 11px}
.categories ul{list-style:none}
.categories li{height:33px;border-bottom:1px solid #e3e3e3;font-size:11.5px;color:#222;display:flex;align-items:center;padding-left:20px;position:relative}
.categories li::before{content:"";position:absolute;left:11px;top:15px;width:2px;height:2px;background:#333}
.categories li:last-child{border-bottom:none}

/* course cards */
.course-card{top:698px;width:174px;height:315px;background:#fff;border:1px solid #d6d6d6;border-radius:3px;box-shadow:0 1px 3px rgba(0,0,0,.2)}
.course-thumb{position:absolute;left:9px;top:7px;width:155px;height:134px;background:linear-gradient(160deg,#f8c025,#f4b318)}
.course-stats{position:absolute;left:0;top:148px;width:100%;height:34px;display:flex;background:#eaeaea;border-top:1px solid #ccc;border-bottom:1px solid #ccc}
.stat-cat{width:84px;border-right:1px solid #ccc;font-size:11px;color:#222;padding:6px 0 0 16px;line-height:12px}
.stat-views{flex:1;text-align:center;font-weight:700;font-size:11px;color:#222;padding-top:3px}
.stat-views svg{display:block;margin:0 auto 2px}
.reviews{position:absolute;top:187px;width:100%;text-align:center;font-size:11px;color:#222}
.stars{display:flex;justify-content:center;gap:1px;margin-top:2px}
.course-body{position:absolute;left:14px;top:220px;width:152px}
.course-title{font-size:10.5px;line-height:12.5px;color:#222}
.course-author{margin-top:1px;font-size:10px;line-height:12px;color:#222}
.course-author span{font-size:8.5px;color:#666}
.btn-details{position:absolute;left:12px;top:281px;width:148px;height:25px;background:linear-gradient(#8a8a8a,#666);border-radius:3px;color:#fff;font-size:10px;font-weight:700;display:flex;align-items:center;justify-content:center;gap:6px;letter-spacing:.3px}

/* organisations */
.org-title{left:291px;top:1034px;font-family:"Raleway",sans-serif;font-weight:500;font-size:15.5px;color:var(--orange)}
.org-text{left:291px;top:1055px;width:560px;font-size:11px;line-height:16px;color:#222}

/* footer */
.site-footer{left:0;top:1121px;width:941px;height:79px;background:var(--footer)}
.footer-links{left:86px;top:1136px;font-size:11px;line-height:17px;color:#ddd}
.site-footer .brand{position:absolute;left:703px;top:20px;color:#f2f2f2;font-size:31px}
</style>
</head>
<body>

<header class="site-header abs">
  <div class="brand abs"><span class="brand-dot"></span>Brivora</div>
  <div class="btn-lang abs">English(US)</div>
  <div class="btn-signin abs">Sign In</div>
</header>

<div class="hero-bg abs" role="img" aria-label="Soft-focus warm yellow background image for the hero banner"></div>
<h1 class="hero-title abs">YOUR LEARNING JOURNEY STARTS HERE</h1>
<p class="hero-sub abs">facilitating elegant e-learning and mixed learning solutions</p>

<form class="beta-card abs">
  <h2>Join Our Beta Limited Availability</h2>
  <div class="field field-email">Email Address</div>
  <div class="field field-reason">Reason for Interest</div>
  <div class="btn-join">Join Beta</div>
</form>

<div class="search-band abs"></div>
<div class="search-input abs">What Can We Help You Learn Today?</div>
<div class="search-btn abs">Search</div>

<div class="section-title abs"><span class="rule"></span><h2>Learning Packages</h2><span class="rule"></span></div>

<aside class="categories abs">
  <h3>Categories</h3>
  <ul>
    <li>Business and Finance</li>
    <li>Marketing</li>
    <li>IT &amp; Software</li>
    <li>Lifestyle</li>
    <li>Personal Development</li>
    <li>Photography</li>
    <li>Health and Fitness</li>
    <li>Education and Teaching</li>
    <li>Music</li>
    <li>Hotels and Hospitality</li>
  </ul>
</aside>

<svg width="0" height="0" style="position:absolute">
  <defs>
    <symbol id="star" viewBox="0 0 20 20"><polygon points="10,1 12.6,7 19,7.4 14,11.6 15.6,18 10,14.5 4.4,18 6,11.6 1,7.4 7.4,7"/></symbol>
    <symbol id="eye" viewBox="0 0 20 12"><path d="M1 6C4 1 16 1 19 6C16 11 4 11 1 6Z" fill="none" stroke="#555" stroke-width="1.6"/><circle cx="10" cy="6" r="2.5" fill="#555"/></symbol>
  </defs>
</svg>

<article class="course-card abs" style="left:291px">
  <div class="course-thumb" role="img" aria-label="Course cover artwork for Nepali Snacks – Speaking Nepali Fundamentals"></div>
  <div class="course-stats"><div class="stat-cat">Language<br>and...</div><div class="stat-views"><svg width="14" height="9"><use href="#eye"/></svg>Views 1417</div></div>
  <div class="reviews">Reviews
    <div class="stars"><svg width="12" height="12" fill="#f5b50a"><use href="#star"/></svg><svg width="12" height="12" fill="#f5b50a"><use href="#star"/></svg><svg width="12" height="12" fill="#f5b50a"><use href="#star"/></svg><svg width="12" height="12" fill="#f5b50a"><use href="#star"/></svg><svg width="12" height="12" fill="#999"><use href="#star"/></svg></div>
  </div>
  <div class="course-body">
    <p class="course-title">Speaking Nepali Fundamentals Suite by Lorne Pike Vell</p>
    <p class="course-author">by <span>Lorne Pike</span></p>
  </div>
  <div class="btn-details"><svg width="18" height="8"><rect x="0" y="1" width="6" height="6" fill="#fff"/><rect x="8" y="1" width="10" height="1.4" fill="#fff"/><rect x="8" y="3.3" width="10" height="1.4" fill="#fff"/><rect x="8" y="5.6" width="10" height="1.4" fill="#fff"/></svg>DETAILS</div>
</article>

<article class="course-card abs" style="left:489px">
  <div class="course-thumb" role="img" aria-label="Course cover artwork for Nepali Snacks – Speaking Nepali Fundamentals"></div>
  <div class="course-stats"><div class="stat-cat">Language<br>and...</div><div class="stat-views"><svg width="14" height="9"><use href="#eye"/></svg>Views 1417</div></div>
  <div class="reviews">Reviews
    <div class="stars"><svg width="12" height="12" fill="#f5b50a"><use href="#star"/></svg><svg width="12" height="12" fill="#f5b50a"><use href="#star"/></svg><svg width="12" height="12" fill="#f5b50a"><use href="#star"/></svg><svg width="12" height="12" fill="#f5b50a"><use href="#star"/></svg><svg width="12" height="12" fill="#999"><use href="#star"/></svg></div>
  </div>
  <div class="course-body">
    <p class="course-title">Speaking Nepali Fundamentals Suite by Lorne Pike Vell</p>
    <p class="course-author">by <span>Lorne Pike</span></p>
  </div>
  <div class="btn-details"><svg width="18" height="8"><rect x="0" y="1" width="6" height="6" fill="#fff"/><rect x="8" y="1" width="10" height="1.4" fill="#fff"/><rect x="8" y="3.3" width="10" height="1.4" fill="#fff"/><rect x="8" y="5.6" width="10" height="1.4" fill="#fff"/></svg>DETAILS</div>
</article>

<article class="course-card abs" style="left:688px">
  <div class="course-thumb" role="img" aria-label="Course cover artwork for Nepali Snacks – Speaking Nepali Fundamentals"></div>
  <div class="course-stats"><div class="stat-cat">Language<br>and...</div><div class="stat-views"><svg width="14" height="9"><use href="#eye"/></svg>Views 1417</div></div>
  <div class="reviews">Reviews
    <div class="stars"><svg width="12" height="12" fill="#f5b50a"><use href="#star"/></svg><svg width="12" height="12" fill="#f5b50a"><use href="#star"/></svg><svg width="12" height="12" fill="#f5b50a"><use href="#star"/></svg><svg width="12" height="12" fill="#f5b50a"><use href="#star"/></svg><svg width="12" height="12" fill="#999"><use href="#star"/></svg></div>
  </div>
  <div class="course-body">
    <p class="course-title">Speaking Nepali Fundamentals Suite by Lorne Pike Vell</p>
    <p class="course-author">by <span>Lorne Pike</span></p>
  </div>
  <div class="btn-details"><svg width="18" height="8"><rect x="0" y="1" width="6" height="6" fill="#fff"/><rect x="8" y="1" width="10" height="1.4" fill="#fff"/><rect x="8" y="3.3" width="10" height="1.4" fill="#fff"/><rect x="8" y="5.6" width="10" height="1.4" fill="#fff"/></svg>DETAILS</div>
</article>

<h3 class="org-title abs">Learning for Organisations and Educational Institutions.</h3>
<p class="org-text abs">Launching Soon! - Brivora will be launching services to integrate Brivora's learning platform into Organisations and Learning Institutes to support Online, Interactive and Blended Learning.</p>

<footer class="site-footer abs">
  <div class="brand"><span class="brand-dot"></span>Brivora</div>
</footer>
<div class="footer-links abs">Copyright © 2015 Brivora.example<br>Terms of Use<br>Privacy Policy</div>

</body>
</html>
```